Visit card

Industry/Entity Type

Health Care

Contact Information for Business Card

O VITALIS SYSTEMS
Odile Brevard - chef de Projet

Requirements
Must have
• 318 Gaston Lemaire Street 59710 BRELANCOURT Tel: 33 (0) 327 481 605 Mobile: 06 42 19 37 64 Web: www.quorvexsystems.example Contact: o.brevard@o-vitalissystems.example
Should not have
• Respect for color

```html
<!DOCTYPE html>
<html lang="fr">
<head>
<meta charset="utf-8">
<title>O Vitalis Systems – Carte de visite</title>
<link href="https://fonts.googleapis.com/css2?family=Lato:wght@400;700&family=Montserrat:wght@600;700&display=swap" rel="stylesheet">
<style>
  :root {
    --stage: #1c1c1e;
    --card: #1a1a1a;
    --card-edge: #262626;
    --red: #e2202c;
    --white: #ffffff;
    --soft: #e6e6e6;
    --rule: #cfcfcf;
  }
  * { box-sizing: border-box; margin: 0; padding: 0; }
  html, body { width: 1200px; height: 900px; overflow: hidden; }
  body {
    background: var(--stage);
    font-family: "Lato", Arial, sans-serif;
    position: relative;
  }
  .card {
    position: absolute;
    left: 250px;
    width: 700px;
    height: 400px;
    background: var(--card);
    border: 1px solid var(--card-edge);
    box-shadow: 0 12px 30px rgba(0,0,0,.55);
    overflow: hidden;
  }
  .card--front { top: 40px; }
  .card--back { top: 460px; }

  .pattern-field {
    position: absolute; inset: 0;
    background: linear-gradient(115deg, #151515 0%, #1f1f1f 45%, #3a3a3a 100%);
  }
  .front-mark {
    position: absolute; left: 50%; top: 50%;
    transform: translate(-50%, -50%);
    display: flex; align-items: center; gap: 10px;
  }
  .front-mark__dot {
    width: 34px; height: 34px; border-radius: 50%;
    background: var(--red); border: 5px solid var(--white);
  }
  .front-mark__name {
    font-family: "Montserrat", Arial, sans-serif;
    font-weight: 700; font-size: 15px; letter-spacing: 1px;
    color: var(--white);
  }

  .brand {
    position: absolute; left: 60px; top: 150px;
    display: flex; align-items: center; gap: 16px;
  }
  .brand__dot {
    width: 74px; height: 74px; border-radius: 50%;
    background: var(--red); border: 12px solid var(--white);
  }
  .brand__name {
    font-family: "Montserrat", Arial, sans-serif;
    font-weight: 700; font-size: 30px; line-height: 1.05;
    color: var(--red);
  }

  .divider {
    position: absolute; left: 372px; top: 110px;
    width: 2px; height: 190px; background: var(--rule);
  }

  .contact {
    position: absolute; left: 400px; top: 100px;
    color: var(--soft);
  }
  .contact__name {
    font-family: "Lato", Arial, sans-serif;
    font-weight: 700; font-size: 24px; color: var(--red);
    text-transform: uppercase; letter-spacing: .5px;
  }
  .contact__role { font-size: 16px; margin-top: 2px; }
  .contact__address { font-size: 16px; line-height: 1.3; margin-top: 12px; }
  .contact__list { list-style: none; margin-top: 12px; font-size: 16px; line-height: 1.55; }
  .contact__list li { display: flex; align-items: center; gap: 8px; white-space: nowrap; }
  .icon { width: 12px; height: 12px; flex: none; }
  .icon path, .icon circle, .icon rect { fill: none; stroke: var(--red); stroke-width: 1.6; }
</style>
</head>
<body>

<section class="card card--front">
  <div class="pattern-field" role="img" aria-label="Motif gaufré répété de la marque sur fond noir"></div>
  <div class="front-mark">
    <span class="front-mark__dot"></span>
    <span class="front-mark__name">O VITALIS SYSTEMS</span>
  </div>
</section>

<section class="card card--back">
  <div class="brand">
    <span class="brand__dot"></span>
    <div class="brand__name">O VITALIS<br>SYSTEMS</div>
  </div>

  <div class="divider"></div>

  <div class="contact">
    <h1 class="contact__name">Odile Brevard</h1>
    <p class="contact__role">Chef de Projet</p>
    <p class="contact__address">318 Gaston Lemaire Street<br>59710 BRELANCOURT</p>
    <ul class="contact__list">
      <li>
        <svg class="icon" viewBox="0 0 12 12"><path d="M2 1 L4.5 1 L5 4 L3.5 5 Q5 8 7 8.5 L8 7 L11 7.5 L11 10 Q6 11.5 1 3 Z"/></svg>
        +33 (0) 327 481 605
      </li>
      <li>
        <svg class="icon" viewBox="0 0 12 12"><rect x="3" y="1" width="6" height="10" rx="1"/></svg>
        06 42 19 37 64
      </li>
      <li>
        <svg class="icon" viewBox="0 0 12 12"><circle cx="6" cy="6" r="5"/><path d="M1 6 H11 M6 1 Q3 6 6 11 Q9 6 6 1"/></svg>
        www.quorvexsystems.example
      </li>
      <li>
        <svg class="icon" viewBox="0 0 12 12"><rect x="1" y="2.5" width="10" height="7"/><path d="M1 2.5 L6 6.5 L11 2.5"/></svg>
        o.brevard@o-vitalissystems.example
      </li>
    </ul>
  </div>
</section>

</body>
</html>
```